Local Motorsports Photography Business Card Design

Looking for a Logo and Business Card design for my father who is a local photographer based in Perth operating under the business name "Pellman Photography". Specializing in Motorsports (Turbo Racers/Rapidcycles/Corvan Rally) and events photography.
Would like it to look professional, while still maintaining a local/personal feel. Color\Design of the Logo and Card are open to your own interpretation, but should limit the color scheme to around 2-3 colors.
Design should be a logo one side and contact details on the rear. The website currently is very simple and a generic template and should not be used as a basis for design.
Industry/Entity Type
Business
Contact Information for Business Card
Name: Marcus Pellman
Website: www.pellmanphotography-example.com.au
Email: marcus@pellmanphotography-example.com.au
Phone: 0400 555 917

```html
<!DOCTYPE html>
<html lang="en">
<head>
<meta charset="utf-8">
<title>Pellman Photography – Business Card</title>
<link href="https://fonts.googleapis.com/css2?family=Exo+2:wght@400;700&display=swap" rel="stylesheet">
<style>
  :root {
    --backdrop: #eeeeee;
    --card-white: #ffffff;
    --card-grey: #eceded;
    --blue-deep: #2ea6e2;
    --blue-light: #85d0f4;
    --ink: #1d1d1f;
    --text-on-blue: #ffffff;
    --brand-blue: #2b9fdc;
  }
  * { box-sizing: border-box; margin: 0; padding: 0; }
  html, body {
    width: 1200px; height: 905px; overflow: hidden;
    background: var(--backdrop);
    font-family: "Exo 2", Arial, sans-serif;
  }
  .canvas { position: relative; width: 1200px; height: 905px; }
  .card {
    position: absolute; top: 310px;
    width: 504px; height: 288px;
    background: var(--card-white);
    box-shadow: 0 6px 18px rgba(0,0,0,0.12);
    overflow: hidden;
  }
  .card--back { left: 70px; }
  .card--front {
    left: 626px; display: flex; align-items: center; justify-content: center;
    background: radial-gradient(circle at 50% 50%, #ffffff 0%, #f3f3f3 100%);
  }
  .contact-panel {
    position: absolute; left: 0; top: 0; bottom: 0; width: 57%;
    background: radial-gradient(ellipse at 70% 40%, var(--blue-light) 0%, var(--blue-deep) 100%);
    color: var(--text-on-blue);
    padding: 52px 16px 0 34px;
  }
  .accent-tab {
    position: absolute; left: 30px; top: 0; width: 22px; height: 42px;
    background: var(--ink);
  }
  .person-name { font-size: 15px; font-weight: 400; letter-spacing: 0.08em; text-transform: uppercase; }
  .person-role { font-size: 13px; margin-top: 2px; }
  .contact-list { list-style: none; margin-top: 34px; font-size: 10px; line-height: 1.9; }
  .contact-list li { display: flex; align-items: center; gap: 7px; white-space: nowrap; }
  .contact-list svg { width: 10px; height: 10px; flex: none; fill: var(--text-on-blue); }
  .address { margin-top: 14px; font-size: 12px; letter-spacing: 0.02em; }
  .logo-side {
    position: absolute; left: 57%; top: 0; right: 0; bottom: 0;
    background: radial-gradient(circle at 50% 50%, #ffffff 0%, var(--card-grey) 100%);
    display: flex; align-items: center; justify-content: center;
  }
  .brand {
    display: flex; align-items: center; gap: 8px;
    font-weight: 700; color: var(--ink); white-space: nowrap;
  }
  .brand-dot { width: 11px; height: 11px; border-radius: 50%; background: var(--brand-blue); flex: none; }
  .logo-side .brand { font-size: 15px; }
  .card--front .brand { font-size: 30px; gap: 10px; }
  .card--front .brand-dot { width: 18px; height: 18px; }
</style>
</head>
<body>
<main class="canvas">
  <section class="card card--back" aria-label="Business card, contact side">
    <div class="contact-panel">
      <span class="accent-tab"></span>
      <p class="person-name">Marcus Pellman</p>
      <p class="person-role">Managing Director</p>
      <ul class="contact-list">
        <li><svg viewBox="0 0 10 10"><path d="M2 0h3l1 3-1.5 1a6 6 0 0 0 1.5 1.5L7 4l3 1v3l-1 2C4 10 0 6 0 1z"/></svg>0400 555 917</li>
        <li><svg viewBox="0 0 10 10"><rect x="0" y="2" width="10" height="7" rx="1"/></svg>marcus@pellmanphotography-example.com.au</li>
        <li><svg viewBox="0 0 10 10"><circle cx="5" cy="5" r="5"/></svg>www.pellmanphotography-example.com.au</li>
      </ul>
      <p class="address">27 Harbour Lane, Perth WA 6000</p>
    </div>
    <div class="logo-side">
      <div class="brand"><span class="brand-dot"></span>Pellman Photography</div>
    </div>
  </section>

  <section class="card card--front" aria-label="Business card, logo side">
    <div class="brand"><span class="brand-dot"></span>Pellman Photography</div>
  </section>
</main>
</body>
</html>
```